MRT Property - Business Cards

Looking for a business card & general letterhead, signage etc design for our new logo.

Colours:
000a20
0056a2
00b5ef
0088ce
68cef2

Fonts:
Poppins
Karla

Please keep look and feel of new brand - example in the zip package I sent.

```html
<!DOCTYPE html>
<html lang="en">
<head>
<meta charset="utf-8">
<title>MRT Property – Business Cards</title>
<link rel="stylesheet" href="https://fonts.googleapis.com/css2?family=Poppins:wght@500;600;700&family=Karla:wght@400;500&display=swap">
<style>
  :root {
    --navy: #000a20;
    --card-navy: #0e1428;
    --royal: #0056a2;
    --cyan: #00b5ef;
    --mid: #0088ce;
    --sky: #68cef2;
    --ink: #3a3f48;
    --paper: #ffffff;
    --stage: #3d3d3d;
  }
  * { margin: 0; padding: 0; box-sizing: border-box; }
  html, body { width: 1200px; height: 803px; overflow: hidden; }
  body {
    background: var(--stage);
    display: flex;
    align-items: center;
    justify-content: center;
    gap: 40px;
    font-family: "Karla", sans-serif;
  }
  .card {
    position: relative;
    width: 520px;
    height: 298px;
    border-radius: 18px;
    overflow: hidden;
  }
  .card--front { background: var(--paper); }
  .card--back { background: var(--card-navy); }

  .front-waves { position: absolute; inset: 0; width: 100%; height: 100%; }

  .brand {
    position: absolute;
    left: 28px;
    top: 100px;
    display: flex;
    align-items: center;
    gap: 9px;
  }
  .brand__dot {
    width: 14px; height: 14px; border-radius: 50%;
    background: var(--mid);
  }
  .brand__name {
    font-family: "Poppins", sans-serif;
    font-weight: 700;
    font-size: 24px;
    color: var(--royal);
    letter-spacing: 0.3px;
  }

  .divider {
    position: absolute;
    left: 250px;
    top: 30px;
    width: 1px;
    height: 150px;
    background: linear-gradient(to bottom, rgba(0,0,0,0), rgba(0,0,0,0.18), rgba(0,0,0,0));
  }

  .contact {
    position: absolute;
    left: 268px;
    top: 28px;
  }
  .contact__name {
    font-family: "Poppins", sans-serif;
    font-weight: 700;
    font-size: 19px;
    color: var(--royal);
    line-height: 1.1;
  }
  .contact__role {
    font-size: 12px;
    color: var(--cyan);
    margin-bottom: 8px;
  }
  .contact__address {
    font-size: 11.5px;
    color: var(--ink);
    line-height: 1.3;
    margin-bottom: 6px;
  }
  .contact__list { list-style: none; }
  .contact__item {
    display: flex;
    align-items: center;
    gap: 7px;
    font-size: 11.5px;
    color: var(--ink);
    line-height: 1.35;
  }
  .contact__icon { width: 10px; height: 10px; flex: none; }

  .back-brand {
    position: absolute;
    left: 0; right: 0; top: 112px;
    text-align: center;
    font-family: "Poppins", sans-serif;
    font-weight: 700;
    font-size: 34px;
    color: var(--sky);
    letter-spacing: 0.5px;
  }
  .back-url {
    position: absolute;
    left: 0; right: 0; bottom: 30px;
    text-align: center;
    font-size: 13px;
    color: var(--paper);
    letter-spacing: 0.3px;
  }
</style>
</head>
<body>

  <section class="card card--front" aria-label="Business card front">
    <svg class="front-waves" viewBox="0 0 520 298" preserveAspectRatio="none" aria-hidden="true">
      <path d="M0 298 L0 262 C220 258 400 220 520 130 L520 298 Z" fill="var(--cyan)"/>
      <path d="M0 298 L0 272 C225 268 405 230 520 142 L520 298 Z" fill="var(--paper)"/>
      <path d="M0 298 L0 276 C228 272 408 234 520 147 L520 298 Z" fill="var(--royal)"/>
    </svg>

    <div class="brand">
      <span class="brand__dot"></span>
      <span class="brand__name">MRT Property</span>
    </div>

    <div class="divider"></div>

    <div class="contact">
      <p class="contact__name">Daniel Hart</p>
      <p class="contact__role">President</p>
      <p class="contact__address">1420 Willowmere Road<br>Lakeview, Canada 58210</p>
      <ul class="contact__list">
        <li class="contact__item">
          <svg class="contact__icon" viewBox="0 0 10 10"><path d="M2 1 L4 1 L4.6 3 L3.4 3.8 C4 5.2 4.8 6 6.2 6.6 L7 5.4 L9 6 L9 8 C5 8.6 1.4 5 2 1 Z" fill="var(--royal)"/></svg>
          555-210-4871
        </li>
        <li class="contact__item">
          <svg class="contact__icon" viewBox="0 0 10 10"><rect x="1" y="2" width="8" height="6" fill="none" stroke="var(--royal)" stroke-width="1.2"/></svg>
          555-210-4872
        </li>
        <li class="contact__item">
          <svg class="contact__icon" viewBox="0 0 10 10"><rect x="1" y="2" width="8" height="6" fill="var(--royal)"/><path d="M1 2 L5 5.5 L9 2" fill="none" stroke="var(--paper)" stroke-width="0.9"/></svg>
          info@MRT.com
        </li>
        <li class="contact__item">
          <svg class="contact__icon" viewBox="0 0 10 10"><circle cx="5" cy="5" r="4" fill="var(--royal)"/></svg>
          www.MRT.com
        </li>
      </ul>
    </div>
  </section>

  <section class="card card--back" aria-label="Business card back">
    <p class="back-brand">MRT Property</p>
    <p class="back-url">www.MRT.com</p>
  </section>

</body>
</html>
```